Poster - gross für Messestand VORALIS
Zielgruppe
Wir sind ein junges Beratungs- und Softwareentwicklungsunternehmen für Business Analytics & Big-Data Lösungen (Mathematiker). Business Analytics ist ein interdisziplinäres Gebiet, mit dem Ziel unternehmerische Entscheidungen und Prozesse durch die kombinierte Anwendung von detaillierten Datenanalysen, Wahrscheinlichkeitsprozessen, Optimierungsmodelle und die Nutzung von modernsten IT Technologien zu optimieren.
Zielgruppe aus der Messe: Marketingleiter, Entscheider grosser E-commerce Unternehmen, die entscheiden müssen, wo Sie das Marketing Budget am effektivsten invenstieren
Produkt: Convertion Atrribution siehe case study http://www.kordwig-tln.example/projects_de.html
Image der Firma: Jung, erfolgreich, Mathematiker, absulut professionell, innovative, sehr international
Messestand: Standart, weisse Wände, grauer Teppich,
Aufgabenstellung
Poster soll als Hintergrund eines Messestandes sein. Es soll ein Hingucker mit ansprechendem Fototeil sein und Leiste mit mainpoints.
zum Beispiel eine Idee:
Bild: Bernhard Quellmar oder jemand, der für verrückten, innovative, creative denkenden Intelektueller steht ( Mathematiker?) und bekannt ist? Offen fúr Ideen!
Slogan ( bei Bernhard Quellmar z.B.): Success is not relative!
Text:
Kordwig TLN your Business Analytics partner, providing you with state-of-the-art Business Analytics & Big Data solutions for:
- conversion attribution
- mixed-media models
- individual customer offer
- churn reduction strategies
- data mining
- demand forecasting
Masse mindestens DINA 0 am leibesten grösser 1,50 x 2m

```html
<!DOCTYPE html>
<html lang="en">
<head>
<meta charset="utf-8">
<title>Kordwig TLN – Success is not relative</title>
<link rel="stylesheet" href="https://fonts.googleapis.com/css2?family=Alfa+Slab+One&family=Open+Sans:wght@400;600;700;800&display=swap">
<style>
  :root {
    --navy-deep: #1f2f4a;
    --navy: #2f4468;
    --navy-light: #5f7898;
    --shirt: #284a7a;
    --skin: #c29c84;
    --board: #2b2b2b;
    --board-frame: #6b4a2c;
    --chalk: #f2f2f2;
    --white: #ffffff;
    --red: #c8102e;
    --ink: #3a3a3a;
    --ink-soft: #6a6a6a;
    --rule: #bdbdbd;
  }
  * { box-sizing: border-box; margin: 0; padding: 0; }
  html, body { width: 968px; height: 1200px; overflow: hidden; background: var(--white); }
  .poster {
    position: relative;
    width: 968px;
    height: 1200px;
    background: var(--white);
    font-family: "Open Sans", Arial, sans-serif;
    color: var(--ink);
  }
  .hero {
    position: absolute;
    inset: 0 0 auto 0;
    height: 840px;
    background: radial-gradient(ellipse at 78% 28%, var(--navy-light) 0%, var(--navy) 48%, var(--navy-deep) 100%);
    overflow: hidden;
  }
  .hero-portrait {
    position: absolute;
    inset: 0;
    background:
      radial-gradient(ellipse 17% 26% at 75% 34%, var(--skin) 0%, rgba(194,156,132,.55) 55%, rgba(194,156,132,0) 100%),
      radial-gradient(ellipse 40% 30% at 80% 100%, var(--shirt) 0%, rgba(40,74,122,.6) 60%, rgba(40,74,122,0) 100%);
  }
  .quote-board {
    position: absolute;
    left: 80px;
    top: 45px;
    width: 440px;
    height: 265px;
    background: var(--board);
    border: 12px solid var(--board-frame);
    border-radius: 4px;
    box-shadow: 0 8px 20px rgba(0,0,0,.4);
    padding: 26px 28px;
    transform: rotate(-2deg);
  }
  .quote-text {
    color: var(--chalk);
    font-weight: 700;
    font-size: 30px;
    line-height: 1.22;
  }
  .quote-author-photo {
    position: absolute;
    left: 24px;
    bottom: 18px;
    width: 86px;
    height: 72px;
    background: linear-gradient(135deg, #8a8a8a, #3e3e3e);
  }
  .quote-author {
    position: absolute;
    right: 26px;
    bottom: 26px;
    color: var(--chalk);
    font-size: 15px;
    font-weight: 600;
  }
  .headline {
    position: absolute;
    left: 100px;
    top: 545px;
    color: var(--white);
    text-shadow: 0 3px 8px rgba(0,0,0,.35);
  }
  .headline-main,
  .headline-sub {
    display: block;
    font-family: "Alfa Slab One", Georgia, serif;
    font-weight: 400;
    line-height: 1;
  }
  .headline-main { font-size: 118px; letter-spacing: 1px; }
  .headline-sub { font-size: 74px; margin-top: 6px; }
  .headline-claim {
    font-weight: 700;
    font-size: 44px;
    line-height: 1.2;
    margin-top: 10px;
  }
  .info {
    position: absolute;
    left: 0;
    top: 840px;
    width: 100%;
    height: 320px;
    padding: 26px 60px 0 60px;
  }
  .info-lead {
    color: var(--red);
    font-weight: 700;
    font-size: 26px;
  }
  .info-intro {
    font-size: 21px;
    line-height: 1.3;
    margin-top: 4px;
  }
  .services {
    display: grid;
    grid-template-columns: 330px 330px;
    grid-auto-flow: column;
    grid-template-rows: repeat(3, auto);
    column-gap: 30px;
    margin-top: 14px;
    list-style: none;
    font-size: 18px;
    line-height: 1.5;
  }
  .services li::before {
    content: "";
    display: inline-block;
    width: 9px;
    height: 9px;
    background: var(--red);
    margin-right: 10px;
    vertical-align: middle;
  }
  .brand {
    position: absolute;
    left: 60px;
    bottom: 22px;
    font-weight: 700;
    font-size: 42px;
    line-height: 1.2;
    color: var(--ink);
  }
  .web {
    position: absolute;
    right: 40px;
    bottom: 30px;
    font-size: 15px;
    color: var(--ink-soft);
  }
  .footer-rule {
    position: absolute;
    left: 0;
    top: 1160px;
    width: 100%;
    height: 4px;
    background: var(--rule);
  }
  .footer-band {
    position: absolute;
    left: 0;
    top: 1168px;
    width: 100%;
    height: 32px;
    background: var(--red);
  }
</style>
</head>
<body>
  <main class="poster">
    <section class="hero">
      <div class="hero-portrait" role="img" aria-label="Portrait photo of a young man in a blue shirt smiling thoughtfully"></div>

      <div class="quote-board">
        <p class="quote-text">Make everything<br>as simple as possible,<br>but not simpler.</p>
        <div class="quote-author-photo" role="img" aria-label="Small portrait photo of the quoted scientist"></div>
        <p class="quote-author">Bernhard Quellmar</p>
      </div>

      <div class="headline">
        <h1>
          <span class="headline-main">SUCCESS</span>
          <span class="headline-sub">IS NOT RELATIVE.</span>
        </h1>
        <p class="headline-claim">Make smarter Decisions.</p>
      </div>
    </section>

    <section class="info">
      <p class="info-lead">Kordwig TLN – your Business Analytics partner,</p>
      <p class="info-intro">Providing you with state-of-the-art Business Analytics<br>&amp; Big Data solutions for:</p>
      <ul class="services">
        <li>conversion attribution</li>
        <li>mixed-media models</li>
        <li>individual customer offer</li>
        <li>churn reduction strategies</li>
        <li>data mining</li>
        <li>demand forecasting</li>
      </ul>
      <p class="brand">Kordwig TLN</p>
      <p class="web">www.kordwig-tln.example</p>
    </section>

    <div class="footer-rule"></div>
    <div class="footer-band"></div>
  </main>
</body>
</html>
```